Business Card Design

- one on one personal training
- group personal training
- indoor or outdoor training available
- fitness and health assessments
- personalised fitness programs
- flexible hours for training

I am a Personal Trainer in Perth Australia. I am looking to expand my word of mouth client base.

I would like to see something that uses the colours blue, green and/or yellow.

The final design should reflect the way that I train clients, fun, motivating and perhaps a little quirky?
Updates

update with a logo with the letters MVF thank you

Hi all, Have had some great designs so far. Have decided to go double sided, perhaps to use the back to list my services. Thank you

Please check update brief. Thank you.

Target Market(s)

Professionals, ages 30 to 60

Industry/Entity Type

Training

Contact Information for Business Card

Marla Prentiss
Personal Trainer

0412 807 254
marlafitcoach@quellmail.example
http://www.marlafitcoach.example

Requirements
Must have
• A logo with the letter MVF
Nice to have
• a logo to represent either; fitness, health, change, overall well-being.
Should not have
• Please no weights or lotus flowers!!

```html
<!DOCTYPE html>
<html lang="en">
<head>
<meta charset="utf-8">
<title>Marla Prentiss – Personal Trainer Business Card</title>
<link rel="stylesheet" href="https://fonts.googleapis.com/css2?family=PT+Sans+Narrow:wght@700&family=Source+Sans+3:wght@400;600&display=swap">
<style>
  :root {
    --card-bg: #ffffff;
    --ink: #1e1e1e;
    --brand-blue: #1565b8;
    --brand-green: #43ab3a;
    --brand-yellow: #ffcf0a;
    --dot-teal: #17a098;
    --dot-orange: #f39a2e;
    --dot-yellow: #f7cf0c;
    --dot-lime: #9cc42a;
    --dot-blue: #0a72be;
    --phone-navy: #2b3990;
    --phone-orange: #f28c28;
  }
  * { margin: 0; padding: 0; box-sizing: border-box; }
  html, body {
    width: 1200px;
    height: 824px;
    overflow: hidden;
    background: var(--card-bg);
  }
  .business-card {
    position: relative;
    width: 1200px;
    height: 824px;
    background: var(--card-bg);
    font-family: "Source Sans 3", "Myriad Pro", Arial, sans-serif;
    color: var(--ink);
  }
  .brand-mark {
    position: absolute;
    left: 180px;
    top: 176px;
    width: 220px;
    display: flex;
    align-items: center;
    justify-content: center;
    gap: 12px;
  }
  .brand-mark__square {
    width: 22px;
    height: 22px;
    background: var(--brand-blue);
  }
  .brand-mark__name {
    font-family: "Source Sans 3", Arial, sans-serif;
    font-weight: 600;
    font-size: 100px;
    line-height: 1;
    letter-spacing: -2px;
    color: var(--brand-blue);
  }
  .identity {
    position: absolute;
    left: 80px;
    width: 400px;
    text-align: center;
  }
  .identity__name {
    top: 334px;
    font-family: "PT Sans Narrow", "Myriad Pro Condensed", sans-serif;
    font-weight: 700;
    font-size: 66px;
    line-height: 1;
    letter-spacing: -0.5px;
  }
  .identity__role {
    top: 410px;
    font-size: 34px;
    line-height: 1;
  }
  .identity__phone {
    top: 534px;
    font-size: 30px;
    line-height: 1;
  }
  .phone-label .c1 { color: var(--phone-navy); }
  .phone-label .c2 { color: var(--brand-blue); }
  .phone-label .c3 { color: var(--brand-green); }
  .phone-label .c4 { color: var(--phone-orange); }
  .phone-sep { color: var(--brand-blue); }
  .phone-number .n1 { color: var(--brand-blue); }
  .phone-number .n2 { color: var(--brand-green); }
  .phone-number .n3 { color: var(--phone-orange); }

  .services {
    position: absolute;
    left: 612px;
    top: 342px;
    list-style: none;
  }
  .services__item {
    display: flex;
    align-items: center;
    font-size: 31px;
    line-height: 47.5px;
  }
  .services__item::before {
    content: "";
    width: 17px;
    height: 17px;
    border-radius: 50%;
    margin-right: 16px;
    background: var(--dot);
  }
  .services__item--teal { --dot: var(--dot-teal); }
  .services__item--orange { --dot: var(--dot-orange); }
  .services__item--yellow { --dot: var(--dot-yellow); }
  .services__item--lime { --dot: var(--dot-lime); }
  .services__item--blue { --dot: var(--dot-blue); }

  .contact-line {
    position: absolute;
    top: 700px;
    font-size: 30px;
    line-height: 1;
  }
  .contact-line--email { left: 72px; }
  .contact-line--web { left: 619px; }

  .color-band {
    position: absolute;
    left: 70px;
    bottom: 0;
    width: 1060px;
    height: 40px;
    display: flex;
  }
  .color-band__segment { flex: 1; }
  .color-band__segment--blue { background: var(--brand-blue); }
  .color-band__segment--green { background: var(--brand-green); }
  .color-band__segment--yellow { background: var(--brand-yellow); }
</style>
</head>
<body>
  <main class="business-card">
    <div class="brand-mark">
      <span class="brand-mark__square"></span>
      <span class="brand-mark__name">MVF</span>
    </div>

    <h1 class="identity identity__name">Marla Prentiss</h1>
    <p class="identity identity__role">Personal Trainer</p>
    <p class="identity identity__phone">
      <span class="phone-label"><span class="c1">P</span><span class="c2">h</span><span class="c3">o</span><span class="c2">n</span><span class="c4">e</span></span>
      <span class="phone-sep">:</span>
      <span class="phone-number"><span class="n1">0412</span> <span class="n2">807</span> <span class="n3">254</span></span>
    </p>

    <ul class="services">
      <li class="services__item services__item--teal">One on one personal training</li>
      <li class="services__item services__item--orange">Group personal training</li>
      <li class="services__item services__item--yellow">Indoor or outdoor training available</li>
      <li class="services__item services__item--lime">Fitness and health assessments</li>
      <li class="services__item services__item--blue">Personalised fitness programs</li>
    </ul>

    <p class="contact-line contact-line--email">E-mail: marlafitcoach@quellmail.example</p>
    <p class="contact-line contact-line--web">Website: www.marlafitcoach.example</p>

    <div class="color-band" aria-hidden="true">
      <span class="color-band__segment color-band__segment--blue"></span>
      <span class="color-band__segment color-band__segment--green"></span>
      <span class="color-band__segment color-band__segment--yellow"></span>
    </div>
  </main>
</body>
</html>
```